IT Company requires new Business Card design.

Over the years we have had a few different business card designs. We are now due for new cards across the board for all staff. We felt this would be a good time to start fresh with a new design. Our traditional card simply had our details on the front, and a list of services on the back. We don't particularly need the list of services, we have had cards where the only thing on the rear of the card was our logo.
Feel free to be creative, we would like our tag line "Complete IT Management" to appear at some point, doesn't necessarily have to be with the logo.
I have attached samples and drafts of various previous cards we have used over the years.

```html
<!DOCTYPE html>
<html lang="en">
<head>
<meta charset="utf-8">
<title>Ridgeway Systems – Business Card</title>
<link rel="stylesheet" href="https://fonts.googleapis.com/css2?family=Open+Sans:wght@400;600;700&display=swap">
<style>
  :root {
    --slate: #5f7282;
    --charcoal: #4a4a4a;
    --ink: #3a3a3a;
    --card: #ffffff;
    --backdrop: #e4e4ea;
    --rule: #c9ccd1;
  }
  * { margin: 0; padding: 0; box-sizing: border-box; }
  html, body {
    width: 1200px; height: 987px; overflow: hidden;
    background: var(--backdrop);
    font-family: "Open Sans", sans-serif;
  }
  .stage { position: relative; width: 1200px; height: 987px; }
  .card {
    position: absolute; left: 280px;
    width: 640px; height: 390px;
    background: var(--card);
    border-radius: 22px;
    overflow: hidden;
    box-shadow: 0 6px 18px rgba(0,0,0,0.12);
  }
  .card--front { top: 80px; }
  .card--back { top: 517px; }

  /* front */
  .brand {
    position: absolute; left: 150px; top: 36px;
    display: flex; align-items: center; gap: 18px;
    color: var(--slate); font-weight: 700;
  }
  .brand__mark { width: 54px; height: 54px; background: var(--slate); }
  .brand__name { font-size: 40px; line-height: 1.02; letter-spacing: 1px; }
  .brand__name span { display: block; }

  .person {
    position: absolute; right: 390px; top: 172px;
    text-align: right; color: var(--ink); font-size: 14px; line-height: 1.55;
  }
  .person__name { color: var(--slate); font-size: 20px; font-weight: 700; line-height: 1.3; }
  .divider { position: absolute; left: 266px; top: 170px; width: 1px; height: 128px; background: var(--rule); }

  .contacts {
    position: absolute; left: 282px; top: 168px;
    list-style: none; color: var(--ink); font-size: 15px;
  }
  .contacts li { display: flex; align-items: center; gap: 9px; height: 24px; }
  .contacts svg { width: 15px; height: 15px; fill: var(--charcoal); flex: none; }

  .swoosh { position: absolute; inset: 0; }
  .tagline {
    position: absolute; right: 30px; bottom: 10px;
    color: #fff; font-size: 13px; font-weight: 600; letter-spacing: 4px;
  }

  /* back */
  .back-brand {
    position: absolute; left: 0; right: 0; top: 120px;
    display: flex; justify-content: center; align-items: center; gap: 22px;
    color: var(--slate); font-weight: 700;
  }
  .back-brand .brand__mark { width: 74px; height: 74px; }
  .back-brand .brand__name { font-size: 52px; }
  .back-web {
    position: absolute; left: 0; right: 0; bottom: 48px; text-align: center;
    color: var(--ink); font-size: 17px; letter-spacing: 1px;
  }
</style>
</head>
<body>
<main class="stage">

  <section class="card card--front">
    <svg class="swoosh" viewBox="0 0 640 390" aria-hidden="true">
      <path fill="var(--charcoal)" d="M0,228 C50,290 150,332 300,340 C440,346 560,347 640,348 C560,350 440,350 300,345 C140,340 40,300 0,250 Z"/>
      <path fill="var(--slate)" d="M0,250 C40,300 140,340 300,345 C440,350 560,350 640,348 V390 H0 Z"/>
    </svg>

    <div class="brand">
      <div class="brand__mark"></div>
      <div class="brand__name"><span>RIDGEWAY</span><span>SYSTEMS</span></div>
    </div>

    <div class="person">
      <div class="person__name">Marcus Hale</div>
      <div>Operation Manager</div>
      <div>Unit 7 22 Harbour Lane</div>
      <div>Kelmscott WA 6111</div>
    </div>
    <div class="divider"></div>

    <ul class="contacts">
      <li><svg viewBox="0 0 16 16"><path d="M3 1h3l1.5 4-2 1.3a9 9 0 0 0 4.2 4.2L11 8.5l4 1.5v3a2 2 0 0 1-2 2A12 12 0 0 1 1 3a2 2 0 0 1 2-2z"/></svg>08 9355 0148</li>
      <li><svg viewBox="0 0 16 16"><path d="M4 0h8v16H4z M5.5 2v9h5V2z"/></svg>0412 580 736</li>
      <li><svg viewBox="0 0 16 16"><path d="M4 1h7v4H4z M1 6h14v8H1z M4 9h8v1H4z"/></svg>08 9355 0148</li>
      <li><svg viewBox="0 0 16 16"><path d="M1 3h14v10H1z M2 4l6 5 6-5" stroke="#fff" stroke-width="1"/></svg>marcus@ridgewaysystems.com.au</li>
      <li><svg viewBox="0 0 16 16"><circle cx="8" cy="8" r="7"/><path d="M1 8h14M8 1v14" stroke="#fff" stroke-width="1"/></svg>www.ridgewaysystems.com.au</li>
    </ul>

    <div class="tagline">COMPLETE IT MANAGEMENT</div>
  </section>

  <section class="card card--back">
    <div class="back-brand">
      <div class="brand__mark"></div>
      <div class="brand__name"><span>RIDGEWAY</span><span>SYSTEMS</span></div>
    </div>
    <div class="back-web">www.ridgewaysystems.com.au</div>
  </section>

</main>
</body>
</html>
```